New, modern business card for growing audiology practice

We need a new business card for our audiology practice. Our logo and website have recently changed (more modern) and we want our business cards to reflect this change.
We conduct hearing tests, perform earwax removals, and fit & dispense hearing aids to our patients. We are a family owned practice in which the owner is the one who works directly with the patient. I have attached logos in various formats to use, as well as two ideas I found on this website; as well as a scanned copy of our current logo. Good luck!

Industry/Entity Type

Business

Contact Information for Business Card

Company name: Tolvera Hearing Center
Provider name: Peter Wolstenby, Au.D. F/NSB
Phone number: (440) 683-5127
Address: 837 W. Lindell Ave. Brennock Falls, OH 44961
email: tolverahearing@postvane.com
website: tolverahearing.com

Colors
000000
aaaaaa
dbdbdb
cacaca
9bcb3c
afd23c
cadf82
b1b1b1

Requirements
Must have
• My card must include information in the "details" section. In the attached images, I found a few that I liked and I would like to model after - "brisky bouncin'" and "Sound Method Center".
• Must be horizontal.
• Must include logos provided. I uploaded them in various file formats and various ways.
• Must match logo font, if possible, if not, please get as close as you can.
Nice to have
• I really like the idea of having a color on one side with just the logo and company name and the contact information and provider name on the other side. I also really like the idea of having the main color dominating on the logo/company side with accent of that same color on the contact side of the card.
Should not have
• Must not be vertical.

```html
<!DOCTYPE html>
<html lang="en">
<head>
<meta charset="utf-8">
<title>Tolvera Hearing Center – Business Card</title>
<link rel="stylesheet" href="https://fonts.googleapis.com/css2?family=Lato:wght@400&family=Roboto:wght@400&family=Roboto+Condensed:wght@700&display=swap">
<style>
  :root {
    --backdrop: #e6e3de;
    --card-dark: #1b1c1e;
    --card-light: #f4f4f4;
    --brand-green: #79a33b;
    --ink: #111111;
    --ink-soft: #4a4a4a;
    --white: #ffffff;
    --black: #000000;
  }
  * { box-sizing: border-box; margin: 0; padding: 0; }
  html, body { width: 1200px; height: 960px; overflow: hidden; }
  body { background: var(--backdrop); position: relative; font-family: "Roboto", Arial, sans-serif; }

  .card { position: absolute; width: 600px; height: 343px; border-radius: 20px; overflow: hidden; }

  /* Logo side */
  .card-back { left: 322px; top: 108px; background: var(--card-dark); }
  .card-back .brand-mark {
    position: absolute; left: 0; right: 0; top: 140px; text-align: center;
    font-family: "Lato", sans-serif; font-weight: 400; font-size: 38px;
    letter-spacing: 2px; color: var(--brand-green); text-transform: uppercase; line-height: 1.15;
  }
  .card-back .website {
    position: absolute; left: 0; right: 0; top: 293px; text-align: center;
    font-size: 14px; letter-spacing: 3.6px; color: var(--white);
  }

  /* Contact side */
  .card-front { left: 320px; top: 493px; background: var(--card-light); }
  .company-name {
    position: absolute; right: 34px; top: 42px; display: flex; align-items: center; gap: 10px;
    font-family: "Lato", sans-serif; font-weight: 400; font-size: 22px; color: var(--ink);
    text-transform: uppercase; letter-spacing: 0.3px;
  }
  .company-name .dot { width: 12px; height: 12px; border-radius: 50%; background: var(--brand-green); }

  .provider { position: absolute; left: 35px; top: 131px; }
  .provider-name {
    font-family: "Roboto Condensed", sans-serif; font-weight: 700; font-size: 21px;
    color: var(--brand-green); text-transform: uppercase; line-height: 1.1;
  }
  .provider-title { font-family: "Roboto Condensed", sans-serif; font-weight: 700; font-size: 15px; color: var(--ink); margin-top: 4px; }

  .address { position: absolute; left: 35px; top: 187px; font-style: normal; font-size: 14px; line-height: 19px; color: var(--ink-soft); }
  .contact-list { position: absolute; left: 35px; top: 234px; list-style: none; font-size: 14px; line-height: 20px; color: var(--ink-soft); }
  .contact-list li { display: flex; align-items: center; gap: 9px; }
  .contact-list svg { width: 13px; height: 13px; fill: var(--brand-green); }

  .footer-band { position: absolute; left: 0; right: 0; bottom: 0; height: 33px; display: flex; }
  .footer-band .website-strip {
    width: 450px; background: var(--brand-green); color: var(--white);
    font-size: 14px; letter-spacing: 4px; display: flex; align-items: center; padding-left: 77px;
  }
  .footer-band .accent-strip { flex: 1; background: var(--black); }
</style>
</head>
<body>
  <section class="card card-back" aria-label="Business card, logo side">
    <div class="brand-mark">Tolvera<br>Hearing Center</div>
    <div class="website">www.tolverahearing.com</div>
  </section>

  <section class="card card-front" aria-label="Business card, contact side">
    <div class="company-name"><span class="dot"></span>Tolvera Hearing Center</div>

    <div class="provider">
      <div class="provider-name">Peter Wolstenby</div>
      <div class="provider-title">AU.D. F/NSB</div>
    </div>

    <address class="address">837 W. Lindell Ave.<br>Brennock Falls, OH 44961</address>

    <ul class="contact-list">
      <li>
        <svg viewBox="0 0 24 24" aria-hidden="true"><path d="M6.6 10.8a15.1 15.1 0 0 0 6.6 6.6l2.2-2.2c.3-.3.7-.4 1-.2 1.1.4 2.3.6 3.6.6.6 0 1 .4 1 1V20c0 .6-.4 1-1 1A17 17 0 0 1 3 4c0-.6.4-1 1-1h3.5c.6 0 1 .4 1 1 0 1.3.2 2.5.6 3.6.1.3 0 .7-.2 1z"/></svg>
        (440) 683-5127
      </li>
      <li>
        <svg viewBox="0 0 24 24" aria-hidden="true"><path d="M2 5h20v14H2z M2 5l10 7 10-7" /></svg>
        tolverahearing@postvane.com
      </li>
    </ul>

    <div class="footer-band">
      <div class="website-strip">www.tolverahearing.com</div>
      <div class="accent-strip"></div>
    </div>
  </section>
</body>
</html>
```